We are a recruitment company based in Norwich/Cambridge England.
I have included our company logo which we want to remain the same.

What we are looking for is a new creative Business card which will really stand out!!

Contact Information for Business Card

Harriet Dunmore
email: Harriet@plavex.co.uk
Address: Brackwell House
Fenmoor Enterprise Park
Partridge Way
Norwich
QB9 3KX
Tel:01632 960418

```html
<!DOCTYPE html>
<html lang="en">
<head>
<meta charset="utf-8">
<title>Plavex Business Card</title>
<link href="https://fonts.googleapis.com/css2?family=Jost:wght@400;500;600&display=swap" rel="stylesheet">
<style>
  :root {
    --green: #8cc63f;
    --grey: #77787b;
    --ink: #2b2b2b;
    --paper: #ffffff;
    --backdrop: #3a3a3a;
  }
  * { margin: 0; padding: 0; box-sizing: border-box; }
  html, body { width: 1200px; height: 800px; overflow: hidden; }
  body {
    background: var(--backdrop);
    font-family: "Jost", sans-serif;
    position: relative;
  }
  .card {
    position: absolute;
    left: 320px;
    width: 560px;
    height: 320px;
    background: var(--paper);
    overflow: hidden;
  }
  .card--front { top: 50px; }
  .card--back { top: 420px; }

  .brand { display: flex; align-items: center; gap: 14px; }
  .brand__dot {
    width: 46px; height: 46px; border-radius: 50%;
    background: var(--green);
  }
  .brand__name {
    font-weight: 500;
    font-size: 48px;
    color: var(--grey);
    letter-spacing: 0.5px;
    line-height: 1;
  }

  .card--front .brand { position: absolute; left: 0; right: 0; top: 108px; justify-content: center; }
  .card--front .website {
    position: absolute; left: 0; right: 0; top: 244px;
    text-align: center; font-size: 15px; letter-spacing: 2px; color: var(--grey);
  }

  .card--back .brand { position: absolute; left: 34px; top: 48px; }
  .card--back .brand__dot { width: 40px; height: 40px; }
  .card--back .brand__name { font-size: 40px; }

  .holder { position: absolute; right: 40px; top: 54px; text-align: right; }
  .holder__name { font-size: 26px; font-weight: 600; color: var(--grey); line-height: 1.1; }
  .holder__name .surname { color: var(--green); }
  .holder__role { font-size: 13px; color: var(--ink); margin-top: 2px; }

  .edge-tab {
    position: absolute; right: 0; top: 40px;
    width: 12px; height: 40px; background: var(--green);
    border-radius: 6px 0 0 6px;
  }

  .address {
    position: absolute; right: 40px; top: 158px;
    text-align: right; font-size: 12.5px; line-height: 1.35; color: var(--ink);
  }

  .contacts { position: absolute; left: 42px; top: 210px; list-style: none; }
  .contacts li {
    display: flex; align-items: center; gap: 10px;
    font-size: 15px; color: var(--ink); line-height: 1.45;
  }
  .contacts .highlight { color: var(--green); }
  .contacts svg { width: 13px; height: 13px; flex: none; }

  .decor { position: absolute; inset: 0; pointer-events: none; }
</style>
</head>
<body>

<section class="card card--front" aria-label="Card front">
  <div class="brand">
    <span class="brand__dot"></span>
    <span class="brand__name">Plavex</span>
  </div>
  <p class="website">www.plavex.co.uk</p>
</section>

<section class="card card--back" aria-label="Card back">
  <svg class="decor" viewBox="0 0 560 320" width="560" height="320" aria-hidden="true">
    <line x1="30" y1="200" x2="400" y2="110" stroke="#8cc63f" stroke-width="1.5"/>
    <path d="M0 292 L360 292 C385 292 388 262 420 262 L560 262" fill="none" stroke="#77787b" stroke-width="2.5"/>
    <path d="M0 304 L370 304 C395 304 398 272 430 272 L560 272 L560 320 L0 320 Z" fill="#8cc63f"/>
  </svg>

  <span class="edge-tab"></span>

  <div class="brand">
    <span class="brand__dot"></span>
    <span class="brand__name">Plavex</span>
  </div>

  <div class="holder">
    <p class="holder__name">Harriet <span class="surname">Dunmore</span></p>
    <p class="holder__role">Ceo &amp; Founder</p>
  </div>

  <p class="address">Brackwell House Fenmoor Enterprise Park,<br>Partridge Way Norwich, QB9 3KX</p>

  <ul class="contacts">
    <li>
      <svg viewBox="0 0 16 16"><path d="M4 1 L6.5 4 L5 6 C6 8.5 7.5 10 10 11 L12 9.5 L15 12 L13 15 C7 15 1 9 1 3 Z" fill="#8cc63f"/></svg>
      01632 960418
    </li>
    <li>
      <svg viewBox="0 0 16 16"><rect x="1" y="3" width="14" height="10" fill="#8cc63f"/><path d="M1 3 L8 9 L15 3" fill="none" stroke="#fff" stroke-width="1.3"/></svg>
      Harriet@plavex.co.uk
    </li>
    <li>
      <svg viewBox="0 0 16 16"><circle cx="8" cy="7" r="5.5" fill="none" stroke="#8cc63f" stroke-width="2"/><path d="M4 11 L2 15" stroke="#8cc63f" stroke-width="2"/></svg>
      <span>www.<span class="highlight">plavex</span>.co.uk</span>
    </li>
  </ul>
</section>

</body>
</html>
```